RWT Fittings Ltd Business Cards

We need a business card with our business logo. We provide window and door installations on high-rises in west coast British Colombia, Canada.

I would like my business information and details on one side of the card, and the other side the company name with logo

Target Market(s)

General Contractors

Industry/Entity Type

Construction

Contact Information for Business Card

one side i want my company name and logo in the dark theme logo that i provided

Requirements
Must have
• Marco Peltieri, 16045518293, RWTFittings@mailbox-demo.com, 1407-5194 Linden Row Burnaby BC, V5H 2K9, Owner & Manager

```html
<!DOCTYPE html>
<html lang="en">
<head>
<meta charset="utf-8">
<title>RWT Fittings Ltd — Business Cards</title>
<link rel="stylesheet" href="https://fonts.googleapis.com/css2?family=Roboto:wght@400;500;700&display=swap">
<style>
  :root {
    --stage: #222224;
    --brand-blue: #27a8e0;
    --card-dark: #1f2025;
    --ink-dark: #1c1d22;
    --text-light: #ffffff;
    --text-grey: #a7a9ae;
    --deco-dark: #272a31;
  }
  * { margin: 0; padding: 0; box-sizing: border-box; }
  html, body {
    width: 1200px; height: 780px; overflow: hidden;
    background: var(--stage);
    font-family: "Roboto", Arial, sans-serif;
  }
  .canvas { position: relative; width: 1200px; height: 780px; }

  .card {
    position: absolute;
    width: 580px; height: 331px;
    border-radius: 24px;
    overflow: hidden;
  }

  /* Front: brand side */
  .card--front {
    left: 110px; top: 40px;
    background: var(--brand-blue);
    display: flex; align-items: center; justify-content: center;
  }
  .brand { display: flex; align-items: center; gap: 16px; }
  .brand__mark { width: 26px; height: 26px; }
  .card--front .brand__mark { background: var(--ink-dark); }
  .card--front .brand__name {
    font-size: 44px; font-weight: 700; color: var(--ink-dark);
    letter-spacing: 1px;
  }

  /* Back: details side */
  .card--back {
    left: 510px; top: 409px;
    background: var(--card-dark);
    border-bottom: 6px solid var(--brand-blue);
    border-left: 3px solid var(--brand-blue);
  }
  .card--back .brand { position: absolute; left: 30px; top: 58px; gap: 12px; }
  .card--back .brand__mark { width: 20px; height: 20px; background: var(--brand-blue); }
  .card--back .brand__name {
    font-size: 30px; font-weight: 700; color: var(--brand-blue);
    letter-spacing: 0.5px;
  }

  .backdrop-panel {
    position: absolute; right: 0; top: 0;
    width: 270px; height: 100%;
    background: linear-gradient(135deg, rgba(39,42,49,0) 0%, var(--deco-dark) 45%, var(--deco-dark) 100%);
  }

  .holder {
    position: absolute; right: 34px; top: 92px;
    text-align: right;
  }
  .holder__name { font-size: 27px; font-weight: 700; line-height: 1.1; }
  .holder__first { color: var(--brand-blue); }
  .holder__last { color: var(--text-grey); }
  .holder__role { font-size: 13px; font-weight: 500; color: var(--text-light); margin-top: 2px; }
  .accent-bar {
    position: absolute; right: 0; top: 86px;
    width: 14px; height: 54px; background: var(--brand-blue);
  }

  .contact {
    position: absolute; left: 44px; bottom: 26px;
    color: var(--text-light); font-size: 14px; line-height: 1.35;
  }
  .contact__address { margin-bottom: 12px; }
  .contact__row { display: flex; align-items: center; gap: 10px; }
  .contact__icon { width: 14px; height: 14px; flex: none; }
</style>
</head>
<body>
<main class="canvas">

  <section class="card card--front" aria-label="Card front">
    <div class="brand">
      <span class="brand__mark"></span>
      <span class="brand__name">RWT Fittings Ltd</span>
    </div>
  </section>

  <section class="card card--back" aria-label="Card back">
    <div class="backdrop-panel" role="img" aria-label="Faint dark brand backdrop"></div>

    <div class="brand">
      <span class="brand__mark"></span>
      <span class="brand__name">RWT Fittings Ltd</span>
    </div>

    <div class="holder">
      <p class="holder__name"><span class="holder__first">Marco</span> <span class="holder__last">Peltieri</span></p>
      <p class="holder__role">Owner &amp; Manager</p>
    </div>
    <div class="accent-bar"></div>

    <div class="contact">
      <p class="contact__address">1407-5194 Linden Row<br>Burnaby BC, V5H 2K9</p>
      <p class="contact__row">
        <svg class="contact__icon" viewBox="0 0 24 24" aria-hidden="true">
          <path fill="#27a8e0" d="M6.6 10.8a15.1 15.1 0 0 0 6.6 6.6l2.2-2.2a1 1 0 0 1 1-.25 11.4 11.4 0 0 0 3.6.57 1 1 0 0 1 1 1V20a1 1 0 0 1-1 1A17 17 0 0 1 3 4a1 1 0 0 1 1-1h3.5a1 1 0 0 1 1 1c0 1.25.2 2.46.57 3.6a1 1 0 0 1-.25 1z"/>
        </svg>
        1604 551 8293
      </p>
      <p class="contact__row">
        <svg class="contact__icon" viewBox="0 0 24 24" aria-hidden="true">
          <rect x="2" y="5" width="20" height="14" rx="2" fill="none" stroke="#27a8e0" stroke-width="2"/>
          <path d="M3 6l9 7 9-7" fill="none" stroke="#27a8e0" stroke-width="2"/>
        </svg>
        RWTFittings@mailbox-demo.com
      </p>
    </div>
  </section>

</main>
</body>
</html>
```